Banner ads for LP that work with same theme as below banners

Love the banner ads below. Need more with attached photos. But use the same wording, font as in below banner ads. Should be LP size 1200/627 so I can use for Pixorly and LP. Looking for great ads to use as LP ads. We do lots of ads so it will be worth your time to enter this contest you will be rewarded with a ton of work. Need several banner ads that work together. So maybe 1 of the dresses, 1 of the sweater, 1 of the leggings, 1 of the jacket

Target Market(s)

Women 24-45

Industry/Entity Type

Fashion

Requirements
Must have
• Banner ads that work for LP and Pixorly
Nice to have
• Several options to choose from
Should not have
• not sure

```html
<!DOCTYPE html>
<html lang="en">
<head>
<meta charset="UTF-8">
<title>Our Best Dresses Ever – Shop the Look</title>
<link href="https://fonts.googleapis.com/css2?family=Yesteryear&family=Playfair+Display:wght@500&family=Tinos:wght@400;700&display=swap" rel="stylesheet">
<style>
  :root {
    --bg-light: #ffffff;
    --bg-grey: #e4e4e4;
    --swoosh-brown: #6b4410;
    --swoosh-line: #b9b9b9;
    --base-dark: #3f352c;
    --base-darker: #2a221c;
    --headline: #7b3f48;
    --headline-dark: #4e2a2f;
    --cta: #3a3a3a;
    --chip-brown: #7d5a2c;
    --chip-black: #0b0908;
    --chip-grey: #9b958d;
    --chip-dark: #1c130e;
  }
  html, body {
    margin: 0;
    padding: 0;
    width: 1200px;
    height: 627px;
    overflow: hidden;
    background: var(--bg-light);
  }
  .banner {
    position: relative;
    width: 1200px;
    height: 627px;
    overflow: hidden;
    background: var(--bg-light);
  }
  .banner__art {
    position: absolute;
    inset: 0;
    width: 1200px;
    height: 627px;
  }
  .headline {
    position: absolute;
    left: 0;
    top: 0;
    margin: 0;
    font-weight: normal;
    color: var(--headline);
  }
  .headline__script {
    position: absolute;
    font-family: "Yesteryear", cursive;
    font-size: 78px;
    line-height: 1;
    white-space: nowrap;
    color: var(--headline);
  }
  .headline__script--top { left: 68px; top: 48px; }
  .headline__script--bottom { left: 145px; top: 196px; }
  .headline__product {
    position: absolute;
    left: 55px;
    top: 138px;
    font-family: "Playfair Display", serif;
    font-weight: 500;
    font-size: 48px;
    letter-spacing: 0.34em;
    line-height: 1;
    white-space: nowrap;
    color: var(--headline-dark);
  }
  .cta {
    position: absolute;
    left: 36px;
    top: 500px;
    margin: 0;
    font-family: "Tinos", serif;
    font-size: 39px;
    font-weight: 400;
    line-height: 1;
    color: var(--cta);
    white-space: nowrap;
  }
  .cta strong { font-weight: 700; }
</style>
</head>
<body>
  <main class="banner">
    <svg class="banner__art" viewBox="0 0 1200 627" xmlns="http://www.w3.org/2000/svg">
      <defs>
        <linearGradient id="sky" x1="0" y1="0" x2="0" y2="1">
          <stop offset="0" stop-color="#f2f2f2"/>
          <stop offset="1" stop-color="#dcdcdc"/>
        </linearGradient>
        <linearGradient id="model" x1="0" y1="0" x2="0" y2="1">
          <stop offset="0" stop-color="#c9a27a"/>
          <stop offset="0.35" stop-color="#5a3e35"/>
          <stop offset="0.7" stop-color="#3f5f8f"/>
          <stop offset="1" stop-color="#2e3a58"/>
        </linearGradient>
        <linearGradient id="base" x1="0" y1="0" x2="0" y2="1">
          <stop offset="0" stop-color="var(--base-dark)"/>
          <stop offset="1" stop-color="var(--base-darker)"/>
        </linearGradient>
      </defs>

      <!-- upper field -->
      <path class="field-upper" d="M0 0 H1200 V0 C900 40 700 120 560 200 C400 300 200 400 0 420 Z" fill="url(#sky)"/>

      <!-- colour chips -->
      <g class="colour-chips">
        <rect x="430" y="228" width="105" height="42" rx="5" fill="var(--chip-brown)"/>
        <rect x="430" y="285" width="105" height="73" rx="5" fill="var(--chip-black)"/>
        <rect x="430" y="372" width="105" height="74" rx="5" fill="var(--chip-brown)"/>
        <rect x="430" y="458" width="105" height="73" rx="5" fill="var(--chip-grey)"/>
        <rect x="430" y="545" width="105" height="50" rx="5" fill="var(--chip-dark)"/>
        <rect x="565" y="165" width="105" height="75" rx="5" fill="var(--chip-brown)"/>
        <rect x="565" y="255" width="105" height="75" rx="5" fill="var(--chip-black)"/>
        <rect x="565" y="342" width="105" height="75" rx="5" fill="var(--chip-brown)"/>
        <rect x="565" y="428" width="105" height="74" rx="5" fill="var(--chip-grey)"/>
        <rect x="565" y="515" width="105" height="75" rx="5" fill="var(--chip-dark)"/>
        <rect x="690" y="428" width="105" height="74" rx="5" fill="var(--chip-brown)"/>
        <rect x="690" y="515" width="105" height="75" rx="5" fill="var(--chip-grey)"/>
      </g>

      <!-- brown swoosh -->
      <path class="swoosh" d="M0 418 C200 400 400 300 560 200 C700 115 900 35 1200 0 V16 C920 50 720 130 580 215 C420 315 220 425 0 456 Z" fill="var(--swoosh-brown)"/>
      <path class="swoosh-line" d="M0 470 C230 440 440 330 600 235 C740 150 930 75 1200 38" fill="none" stroke="var(--swoosh-line)" stroke-width="2"/>

      <!-- model photo area -->
      <rect x="805" y="20" width="340" height="590" rx="40" fill="url(#model)" role="img" aria-label="Model wearing a long-sleeved floral lace mini dress in brown and blue"/>

      <!-- base band -->
      <path class="base-line" d="M0 570 C400 560 800 560 1200 552" fill="none" stroke="var(--swoosh-line)" stroke-width="2"/>
      <path class="base-band" d="M0 590 C400 580 800 580 1200 572 V627 H0 Z" fill="url(#base)"/>
    </svg>

    <h1 class="headline">
      <span class="headline__script headline__script--top">Our Best</span>
      <span class="headline__product">DRESSES</span>
      <span class="headline__script headline__script--bottom">Ever!</span>
    </h1>

    <p class="cta"><strong>SHOP</strong> THE <strong>LOOK</strong></p>
  </main>
</body>
</html>
```